New Business Card Design Project

Use the flyer uploaded and website www.brightoakbuilders.com for inspiration.
List Our Services on Backside of business cards
Marcus Delling
Harborline Builders Inc.
Licensed General Contractors
858-471-6093

Contact Information for Business Card

Use the flyer uploaded and website www.brightoakbuilders.com for inspiration. List Our Services on Backside of business cards Marcus Delling Harborline Builders Inc. Licensed General Contractors 858-471-6093

```html
<!DOCTYPE html>
<html lang="en">
<head>
<meta charset="utf-8">
<title>Harborline Builders – Business Cards</title>
<link href="https://fonts.googleapis.com/css2?family=Cinzel:wght@400&family=Hind:wght@400;500&family=Roboto:wght@400;500;700&display=swap" rel="stylesheet">
<style>
  :root {
    --stage: #2b2b2e;
    --card-dark: #232326;
    --card-light: #ffffff;
    --red: #ec1c24;
    --blue: #5585c5;
    --ink: #1b1b1b;
    --white: #ffffff;
  }
  * { margin: 0; padding: 0; box-sizing: border-box; }
  html, body {
    width: 1200px; height: 780px; overflow: hidden;
    background: var(--stage);
  }
  .stage { position: relative; width: 1200px; height: 780px; }
  .card {
    position: absolute; left: 328px; width: 546px; height: 311px;
    border-radius: 22px; overflow: hidden;
  }
  .card--back { top: 63px; background: var(--card-dark); border: 2px solid var(--red); border-top-color: transparent; border-right-color: transparent; }
  .card--front { top: 406px; background: var(--card-light); border: 2px solid var(--red); border-top-color: transparent; border-right-color: transparent; }

  .brand-name {
    position: absolute; font-family: "Cinzel", serif; font-weight: 400;
    white-space: nowrap; transform: translateX(-50%);
  }
  .card--back .brand-name { left: 142px; top: 186px; font-size: 21px; color: var(--white); }
  .card--front .brand-name { left: 120px; top: 180px; font-size: 19px; color: var(--ink); }

  .services { position: absolute; left: 336px; top: 48px; }
  .services__headline {
    font-family: "Roboto", sans-serif; font-weight: 700; font-size: 14.5px;
    line-height: 16px; color: var(--red); text-transform: uppercase;
  }
  .services__lead {
    font-family: "Roboto", sans-serif; font-weight: 700; font-size: 14.5px;
    line-height: 17px; color: var(--blue); text-transform: uppercase; margin-bottom: 8px;
  }
  .services__list { list-style: none; }
  .services__item {
    display: flex; align-items: center; gap: 8px; height: 17.3px;
    font-family: "Hind", sans-serif; font-size: 12px; color: var(--white); letter-spacing: 0.2px;
  }
  .services__item svg { width: 14px; height: 14px; flex: none; }

  .divider { position: absolute; left: 270px; top: 55px; width: 2px; height: 202px; background: var(--red); }
  .contact { position: absolute; left: 320px; top: 72px; }
  .contact__name {
    font-family: "Roboto", sans-serif; font-weight: 700; font-size: 31px; line-height: 32px;
    color: var(--red);
  }
  .contact__role { font-family: "Roboto", sans-serif; font-size: 12.5px; color: var(--ink); margin-top: 1px; }
  .contact__company { font-family: "Roboto", sans-serif; font-size: 12.5px; color: var(--ink); margin-top: 26px; }
  .contact__lines { list-style: none; margin-top: 15px; }
  .contact__line {
    display: flex; align-items: center; gap: 8px; height: 18.5px;
    font-family: "Roboto", sans-serif; font-size: 12.5px; color: var(--ink);
  }
  .contact__line svg { width: 13px; height: 13px; flex: none; }
  .bands { position: absolute; left: 0; top: 270px; width: 546px; height: 22px; }
</style>
</head>
<body>
<main class="stage">

  <section class="card card--back" aria-label="Business card back">
    <div class="brand-name">Harborline Builders</div>
    <div class="services">
      <p class="services__headline">Our services are<br>100% guaranteed</p>
      <p class="services__lead">Specializing in:</p>
      <ul class="services__list">
        <li class="services__item"><svg viewBox="0 0 14 14"><circle cx="7" cy="7" r="6" fill="none" stroke="#ec1c24" stroke-width="1.2"/><path d="M3.5 7l2.5 2.5L12.5 2" fill="none" stroke="#ec1c24" stroke-width="1.6"/></svg>Remodel: Kitchen &amp; Bath</li>
        <li class="services__item"><svg viewBox="0 0 14 14"><circle cx="7" cy="7" r="6" fill="none" stroke="#ec1c24" stroke-width="1.2"/><path d="M3.5 7l2.5 2.5L12.5 2" fill="none" stroke="#ec1c24" stroke-width="1.6"/></svg>Painting: Interior &amp; Exterior</li>
        <li class="services__item"><svg viewBox="0 0 14 14"><circle cx="7" cy="7" r="6" fill="none" stroke="#ec1c24" stroke-width="1.2"/><path d="M3.5 7l2.5 2.5L12.5 2" fill="none" stroke="#ec1c24" stroke-width="1.6"/></svg>Flooring: Carpet, Vinyl, Wood</li>
        <li class="services__item"><svg viewBox="0 0 14 14"><circle cx="7" cy="7" r="6" fill="none" stroke="#ec1c24" stroke-width="1.2"/><path d="M3.5 7l2.5 2.5L12.5 2" fill="none" stroke="#ec1c24" stroke-width="1.6"/></svg>Window &amp; Door Replacement</li>
        <li class="services__item"><svg viewBox="0 0 14 14"><circle cx="7" cy="7" r="6" fill="none" stroke="#ec1c24" stroke-width="1.2"/><path d="M3.5 7l2.5 2.5L12.5 2" fill="none" stroke="#ec1c24" stroke-width="1.6"/></svg>Plumbing: Repairs &amp; Upgrades</li>
        <li class="services__item"><svg viewBox="0 0 14 14"><circle cx="7" cy="7" r="6" fill="none" stroke="#ec1c24" stroke-width="1.2"/><path d="M3.5 7l2.5 2.5L12.5 2" fill="none" stroke="#ec1c24" stroke-width="1.6"/></svg>Energy-Efficient Upgrades</li>
        <li class="services__item"><svg viewBox="0 0 14 14"><circle cx="7" cy="7" r="6" fill="none" stroke="#ec1c24" stroke-width="1.2"/><path d="M3.5 7l2.5 2.5L12.5 2" fill="none" stroke="#ec1c24" stroke-width="1.6"/></svg>Deck &amp; Patio Construction</li>
        <li class="services__item"><svg viewBox="0 0 14 14"><circle cx="7" cy="7" r="6" fill="none" stroke="#ec1c24" stroke-width="1.2"/><path d="M3.5 7l2.5 2.5L12.5 2" fill="none" stroke="#ec1c24" stroke-width="1.6"/></svg>Water &amp; Mold Damage</li>
        <li class="services__item"><svg viewBox="0 0 14 14"><circle cx="7" cy="7" r="6" fill="none" stroke="#ec1c24" stroke-width="1.2"/><path d="M3.5 7l2.5 2.5L12.5 2" fill="none" stroke="#ec1c24" stroke-width="1.6"/></svg>Garage Renovation</li>
      </ul>
    </div>
  </section>

  <section class="card card--front" aria-label="Business card front">
    <div class="brand-name">Harborline Builders</div>
    <div class="divider"></div>
    <div class="contact">
      <h1 class="contact__name">Marcus Delling</h1>
      <p class="contact__role">Licensed General Contractors</p>
      <p class="contact__company">Harborline Builders Inc.</p>
      <ul class="contact__lines">
        <li class="contact__line"><svg viewBox="0 0 14 14"><path d="M3 1.5l2 2.5-1 1.5c.8 1.8 2 3 3.8 3.8l1.5-1 2.5 2-1.2 2C6 11.8 2.2 8 1 3z" fill="#ec1c24"/></svg>858-471-6093</li>
        <li class="contact__line"><svg viewBox="0 0 14 14"><rect x="1" y="3" width="12" height="9" rx="1" fill="#ec1c24"/><path d="M1.5 3.5L7 8l5.5-4.5" fill="none" stroke="#fff" stroke-width="1"/></svg>info@brightoakbuilders.com</li>
        <li class="contact__line"><svg viewBox="0 0 14 14"><circle cx="7" cy="7" r="6" fill="#ec1c24"/><path d="M1 7h12M7 1c-2.5 3-2.5 9 0 12M7 1c2.5 3 2.5 9 0 12" fill="none" stroke="#fff" stroke-width="0.9"/></svg>www.brightoakbuilders.com</li>
      </ul>
    </div>
    <svg class="bands" viewBox="0 0 546 22" preserveAspectRatio="none" aria-hidden="true">
      <path d="M0 0H240Q250 0 258 5L280 20H0Z" fill="#ec1c24"/>
      <path d="M264 0H546V20H298Q290 20 282 15Z" fill="#5585c5"/>
    </svg>
  </section>

</main>
</body>
</html>
```